New business stationairy

I need paper with header and footer and business cards.
I am a Ltd Company and my main field of expertise is QA/QC inspection in the Oil and Gas Industry. I will need all contact detail inserted and a footer with registration number and bank details etc

```html
<!DOCTYPE html>
<html lang="en">
<head>
<meta charset="utf-8">
<title>Halden Verification Services Ltd – Business Card</title>
<link href="https://fonts.googleapis.com/css2?family=Poppins:wght@400;600&display=swap" rel="stylesheet">
<style>
  :root {
    --backdrop: #d9dadd;
    --paper: #ededee;
    --slate: #575a69;
    --blue: #3a73a6;
    --ink: #5a5c66;
    --white: #f4f4f5;
  }
  * { box-sizing: border-box; margin: 0; padding: 0; }
  html, body {
    width: 1200px;
    height: 900px;
    overflow: hidden;
    background: var(--backdrop);
    font-family: "Poppins", sans-serif;
  }
  .sheet {
    width: 1200px;
    height: 900px;
    display: flex;
    align-items: center;
    justify-content: center;
    gap: 36px;
  }
  .card {
    position: relative;
    width: 540px;
    height: 309px;
    background: var(--paper);
    overflow: hidden;
    box-shadow: 0 10px 24px rgba(0,0,0,0.18);
  }

  /* Company name */
  .company-name {
    position: absolute;
    font-size: 18px;
    font-weight: 600;
    letter-spacing: 0.6px;
    line-height: 1.2;
    white-space: nowrap;
    color: var(--blue);
  }

  /* Front */
  .card-front .company-name { left: 44px; top: 48px; }
  .contact {
    position: absolute;
    right: 38px;
    top: 150px;
    text-align: right;
    color: var(--ink);
  }
  .contact-name {
    color: var(--blue);
    font-weight: 600;
    font-size: 15px;
    letter-spacing: 1px;
  }
  .contact-role {
    font-size: 11px;
    margin-bottom: 14px;
  }
  .contact-line {
    font-size: 10.5px;
    line-height: 1.55;
    white-space: nowrap;
  }
  .contact-line .label {
    color: var(--blue);
    font-weight: 600;
  }
  .footer-band {
    position: absolute;
    bottom: 14px;
    height: 18px;
  }
  .footer-band.slate { left: 0; width: 100px; background: var(--slate); }
  .footer-band.blue { left: 108px; right: 0; background: var(--blue); }

  /* Back */
  .card-back svg { position: absolute; inset: 0; }
  .card-back .company-name {
    left: 0;
    right: 0;
    top: 64px;
    text-align: center;
    color: var(--white);
  }
</style>
</head>
<body>
  <main class="sheet">
    <section class="card card-front" aria-label="Business card front">
      <p class="company-name">HALDEN VERIFICATION SERVICES LTD</p>
      <div class="contact">
        <p class="contact-name">MAREN HOLT</p>
        <p class="contact-role">Managing Director</p>
        <p class="contact-line">The Willows, Mill Lane, Ashby, Stourhill, Wessex</p>
        <p class="contact-line"><span class="label">Phone:</span> +07700 900318 · <span class="label">Email:</span> maren@haldenvs.co.uk</p>
      </div>
      <span class="footer-band slate"></span>
      <span class="footer-band blue"></span>
    </section>

    <section class="card card-back" aria-label="Business card back">
      <svg width="540" height="309" viewBox="0 0 540 309" aria-hidden="true">
        <rect class="back-paper" width="540" height="309" fill="var(--paper)"/>
        <path class="back-panel" d="M0 0 H540 V188 L0 168 Z" fill="var(--slate)"/>
        <path class="back-arc" d="M0 206 Q180 222 250 309 H0 Z" fill="var(--blue)"/>
      </svg>
      <p class="company-name">HALDEN VERIFICATION SERVICES LTD</p>
    </section>
  </main>
</body>
</html>
```